RWT Fittings Ltd Business Cards

We need a business card with our business logo. We provide window and door installations on high-rises in west coast British Colombia, Canada.

I would like my business information and details on one side of the card, and the other side the company name with logo

Target Market(s)

General Contractors

Industry/Entity Type

Construction

Contact Information for Business Card

one side i want my company name and logo in the dark theme logo that i provided

Requirements
Must have
• Marco Peltieri, 16045518293, RWTFittings@mailbox-demo.com, 1407-5194 Linden Row Burnaby BC, V5H 2K9, Owner & Manager

```html
<!DOCTYPE html>
<html lang="en">
<head>
<meta charset="utf-8">
<title>RWT Fittings Ltd — Business Card</title>
<link rel="stylesheet" href="https://fonts.googleapis.com/css2?family=Open+Sans:wght@300;400;600;700&display=swap">
<style>
  :root {
    --backdrop: #3a3a3a;
    --card-black: #161616;
    --card-white: #ffffff;
    --brand-blue: #29a8e0;
    --text-light: #f2f2f2;
    --pattern-dark: #1e1e1e;
    --pattern-mid: #262626;
    --brand-size: 21px;
  }
  * { margin: 0; padding: 0; box-sizing: border-box; }
  html, body {
    width: 1200px;
    height: 780px;
    overflow: hidden;
    background: var(--backdrop);
    font-family: "Open Sans", Arial, sans-serif;
  }
  .sheet {
    position: relative;
    width: 1200px;
    height: 780px;
    display: flex;
    align-items: center;
    justify-content: center;
    gap: 48px;
  }
  .card {
    position: relative;
    width: 540px;
    height: 309px;
    overflow: hidden;
    box-shadow: 0 14px 30px rgba(0,0,0,0.45);
  }

  /* Front: contact details */
  .card-front { background: var(--card-white); }
  .card-front .wave { position: absolute; inset: 0; width: 100%; height: 100%; }
  .contact {
    position: absolute;
    left: 30px;
    top: 52px;
    color: var(--text-light);
  }
  .contact-name {
    position: relative;
    padding-left: 16px;
    font-size: 23px;
    font-weight: 700;
    color: var(--brand-blue);
    line-height: 1.1;
  }
  .contact-name::before {
    content: "";
    position: absolute;
    left: 0;
    top: -4px;
    width: 8px;
    height: 34px;
    background: var(--brand-blue);
  }
  .contact-role {
    padding-left: 16px;
    margin-top: 4px;
    font-size: 12px;
    font-weight: 300;
  }
  .contact-address {
    margin-top: 26px;
    font-size: 12px;
    font-weight: 400;
    line-height: 1.5;
  }
  .contact-line {
    display: flex;
    align-items: center;
    gap: 7px;
    margin-top: 8px;
    font-size: 12px;
    font-weight: 400;
  }
  .contact-line + .contact-line { margin-top: 4px; }
  .contact-icon { width: 12px; height: 12px; flex: none; }

  .brand {
    display: flex;
    align-items: center;
    gap: 9px;
  }
  .brand-front {
    position: absolute;
    right: 18px;
    top: 140px;
  }
  .brand-mark {
    width: 18px;
    height: 18px;
    background: var(--brand-blue);
  }
  .brand-name {
    font-size: var(--brand-size);
    font-weight: 700;
    color: var(--brand-blue);
    white-space: nowrap;
  }

  /* Back: brand side */
  .card-back { background: var(--card-black); }
  .back-pattern {
    position: absolute;
    inset: 0;
    background: linear-gradient(135deg, var(--pattern-mid) 0%, var(--pattern-dark) 55%, var(--card-black) 100%);
  }
  .brand-back {
    position: absolute;
    inset: 0;
    justify-content: center;
  }
</style>
</head>
<body>
<main class="sheet">

  <section class="card card-front" aria-label="Card front with contact details">
    <svg class="wave" viewBox="0 0 540 309" preserveAspectRatio="none" aria-hidden="true">
      <path d="M0 0 H330 C300 50 300 120 292 190 C285 250 270 290 235 309 H0 Z" fill="var(--card-black)"/>
      <path d="M330 0 C300 50 300 120 292 190 C285 250 270 290 235 309 H243 C280 290 297 250 304 190 C312 120 314 50 344 0 Z" fill="var(--brand-blue)"/>
    </svg>

    <div class="contact">
      <h1 class="contact-name">Marco Peltieri</h1>
      <p class="contact-role">Owner &amp; Manager</p>
      <p class="contact-address">1407-5194 Linden Row<br>Burnaby BC, V5H 2K9</p>
      <p class="contact-line">
        <svg class="contact-icon" viewBox="0 0 24 24" aria-hidden="true"><path fill="var(--brand-blue)" d="M6.6 10.8a15.1 15.1 0 0 0 6.6 6.6l2.2-2.2a1 1 0 0 1 1-.25 11.4 11.4 0 0 0 3.6.57 1 1 0 0 1 1 1V20a1 1 0 0 1-1 1A17 17 0 0 1 3 4a1 1 0 0 1 1-1h3.5a1 1 0 0 1 1 1c0 1.25.2 2.45.57 3.57a1 1 0 0 1-.25 1Z"/></svg>
        16045518293
      </p>
      <p class="contact-line">
        <svg class="contact-icon" viewBox="0 0 24 24" aria-hidden="true"><rect x="2" y="5" width="20" height="14" rx="1.5" fill="none" stroke="var(--brand-blue)" stroke-width="2"/><path d="M3 6l9 7 9-7" fill="none" stroke="var(--brand-blue)" stroke-width="2"/></svg>
        RWTFittings@mailbox-demo.com
      </p>
    </div>

    <div class="brand brand-front">
      <span class="brand-mark" aria-hidden="true"></span>
      <span class="brand-name">RWT Fittings Ltd</span>
    </div>
  </section>

  <section class="card card-back" aria-label="Card back with company name">
    <div class="back-pattern" role="img" aria-label="Faint tonal pattern of repeated building symbols across the dark background"></div>
    <div class="brand brand-back">
      <span class="brand-mark" aria-hidden="true"></span>
      <span class="brand-name">RWT Fittings Ltd</span>
    </div>
  </section>

</main>
</body>
</html>
```